Maplecrest Disability - Social Security Disability Attorneys

Our company is expanding to attract clients nationwide for our social security disability practice. We have a logo, but I am looking for a creative and elegant letterhead that projects an image of being technologically advanced but still professional enough for the legal field. I am looking for the "wow factor" combined with this is still professional enough for a law practice.

Requesting letterhead and business card design
Updates

Had to update and change the logo. The previous logo had a typo. Please send updates with the new logo for consideration. The letterhead and business cards should be professional enough to be used for a law firm. Thanks.

Industry/Entity Type

Law Practice, Law Firm, Healthcare Industry, Government

Colors

Designer to choose colors to be used in the design.

Requirements
Nice to have
• **Please create a vertical design for the business card**

```html
<!DOCTYPE html>
<html lang="en">
<head>
<meta charset="utf-8">
<title>Maplecrest Disability – Business Card</title>
<link href="https://fonts.googleapis.com/css2?family=Cinzel:wght@600&family=Lato:wght@400;700&display=swap" rel="stylesheet">
<style>
  :root{
    --backdrop:#a3a3a3;
    --brand-blue:#4a74e8;
    --brand-orange:#f9832b;
    --paper:#ffffff;
    --shadow:rgba(0,0,0,.35);
  }
  *{box-sizing:border-box;margin:0;padding:0}
  html,body{width:1200px;height:1200px;overflow:hidden}
  body{background:var(--backdrop);position:relative;font-family:'Lato',sans-serif}
  .card{position:absolute;top:303px;width:370px;height:594px;overflow:hidden;box-shadow:4px 4px 6px var(--shadow)}
  .card-front{left:200px;background:linear-gradient(205deg,var(--brand-orange) 18%,#c98060 36%,var(--brand-blue) 62%)}
  .card-back{left:599px;background:var(--brand-blue)}
  .wordmark{position:absolute;left:0;width:100%;text-align:center;font-family:'Lato',sans-serif;font-weight:700}
  .wordmark-name{font-size:23px;white-space:nowrap}
  .wordmark-tagline{font-size:11px;margin-top:5px;white-space:nowrap}
  .card-front .wordmark{top:512px;color:var(--paper)}
  .back-top{position:absolute;left:0;top:0;width:100%;height:293px;background:var(--paper)}
  .back-top .wordmark{top:150px;color:var(--brand-blue)}
  .divider-band{position:absolute;left:0;top:293px;width:100%;height:5px;background:var(--brand-orange)}
  .divider-dot{position:absolute;left:163px;top:294px;width:44px;height:44px;border-radius:50%;background:var(--brand-orange);border:4px solid var(--paper)}
  .person{position:absolute;top:346px;width:100%;text-align:center;color:var(--paper)}
  .person-name{font-family:'Cinzel',serif;font-weight:600;font-size:24px;line-height:1.1}
  .person-role{font-size:17px;margin-top:1px}
  .contact-icons{position:absolute;top:405px;left:0;width:100%;display:flex;justify-content:center;align-items:center;gap:4px}
  .rule{height:1px;background:var(--paper);width:52px}
  .rule.left{margin-right:3px}.rule.right{margin-left:3px}
  .icon{width:25px;height:25px;border-radius:3px;background:var(--paper);display:flex;align-items:center;justify-content:center}
  .icon svg{width:17px;height:17px}
  .contact-list{position:absolute;top:440px;width:100%;text-align:center;color:var(--paper);font-size:17px;line-height:21.5px;list-style:none}
  .section-rule{position:absolute;top:516px;left:88px;width:194px;height:1px;background:var(--paper)}
  .address{position:absolute;top:526px;width:100%;text-align:center;color:var(--paper);font-size:17px;line-height:21.5px;font-style:normal}
</style>
</head>
<body>
  <section class="card card-front" aria-label="Business card front">
    <div class="wordmark">
      <div class="wordmark-name">Maplecrest Disability</div>
      <div class="wordmark-tagline">Social Security Disability Attorneys</div>
    </div>
  </section>

  <section class="card card-back" aria-label="Business card back">
    <div class="back-top">
      <div class="wordmark">
        <div class="wordmark-name">Maplecrest Disability</div>
        <div class="wordmark-tagline">Social Security Disability Attorneys</div>
      </div>
    </div>
    <div class="divider-band"></div>
    <div class="divider-dot"></div>

    <div class="person">
      <div class="person-name">DANIEL WHITFORD</div>
      <div class="person-role">Managing Director</div>
    </div>

    <div class="contact-icons">
      <span class="rule left"></span>
      <span class="icon" aria-label="Phone"><svg viewBox="0 0 20 20" fill="none" stroke="#4a74e8" stroke-width="1.6"><path d="M3 7c0-2 3-3 7-3s7 1 7 3v1.5h-3.5V7h-7v1.5H3z" fill="#4a74e8"/><rect x="5" y="9" width="10" height="7" rx="1"/><circle cx="10" cy="12.5" r="1.6"/></svg></span>
      <span class="icon" aria-label="Email"><svg viewBox="0 0 20 20" fill="none" stroke="#4a74e8" stroke-width="1.5"><rect x="2.5" y="5" width="15" height="10"/><path d="M2.5 5l7.5 6 7.5-6M2.5 15l5.5-5M17.5 15l-5.5-5"/></svg></span>
      <span class="icon" aria-label="Website"><svg viewBox="0 0 20 20" fill="none" stroke="#4a74e8" stroke-width="1.4"><circle cx="10" cy="10" r="7.5"/><ellipse cx="10" cy="10" rx="3.2" ry="7.5"/><path d="M2.5 10h15"/></svg></span>
      <span class="rule right"></span>
    </div>

    <ul class="contact-list">
      <li>044-555 010 278</li>
      <li>info@maplecrestlaw.com</li>
      <li>www.maplecrestlaw.com</li>
    </ul>
    <div class="section-rule"></div>
    <address class="address">87, Harbor Line Avenue<br>30718, Country Name</address>
  </section>
</body>
</html>
```